Business card for marketing analytics company

Need a business card for new company. I have a logo already that I want to be built into the card and should use those colours

Company is called steered by tallies
Design must bring steered by tallies to life not be a card that could be for anyone with a logo put on it.

Like the front to be fairly clean and uncluttered bringing the logo out with a suitable design on the back of the card.

The logo represents a compass and business growth so those themes along with numbers, analytics , data are appropriate.
I'm often working with creative industries so also needs to reflect the creative side of analytics rather than be very corporate looking.

Target Market(s)

Ad agency, media agency, consumer goods clients

Industry/Entity Type

Market Research

Contact Information for Business Card

Needs to include name, title, email and phone number

Colors
f78f20
f68d4d
ec1f27

Requirements
Must have
• Must bring steered by tallies to life not be a card that could be for anyone with a logo put on it.
• Logo, Correct colours
• Like a design on the back that relates to company name
• Designs for both sides
Should not have
• Please do not just submit logo and a coloured card.
• It needs to have a design element to it
• No black background
• No clear cards - needs front & back

```html
<!DOCTYPE html>
<html lang="en">
<head>
<meta charset="utf-8">
<title>Steered by Tallies – Business Card</title>
<link href="https://fonts.googleapis.com/css2?family=Roboto:wght@400;500&display=swap" rel="stylesheet">
<style>
  :root {
    --backdrop: #e4e4e4;
    --card: #f6f6f6;
    --slate: #3d4650;
    --orange: #e2661c;
    --orange-band: #d8631a;
    --red: #a31f1f;
    --rule: #b9b9b9;
    --ink: #3a3a3a;
  }
  * { margin: 0; padding: 0; box-sizing: border-box; }
  html, body { width: 1200px; height: 576px; overflow: hidden; }
  body {
    background: var(--backdrop);
    font-family: "Roboto", Arial, sans-serif;
    position: relative;
  }
  .card {
    position: absolute;
    top: 138px;
    width: 482px;
    height: 292px;
    background: var(--card);
    border-radius: 12px;
    overflow: hidden;
  }
  .card--front { left: 82px; }
  .card--back { left: 602px; }

  .brand {
    position: absolute;
    display: flex;
    align-items: center;
    gap: 16px;
  }
  .brand__dot {
    border: 4px solid var(--orange);
    border-radius: 50%;
    flex: none;
  }
  .brand__name {
    font-weight: 500;
    color: var(--slate);
    line-height: 1;
    white-space: nowrap;
  }
  .card--front .brand { left: 100px; top: 113px; }
  .card--front .brand__dot { width: 68px; height: 68px; }
  .card--front .brand__name { font-size: 27px; }

  .card--back .brand { right: 22px; top: 40px; gap: 12px; }
  .card--back .brand__dot { width: 52px; height: 52px; border-width: 3px; }
  .card--back .brand__name { font-size: 19px; }

  .holder { position: absolute; left: 24px; top: 134px; }
  .holder__name { font-size: 18px; font-weight: 500; color: var(--red); }
  .holder__title { font-size: 11px; color: var(--ink); margin-top: 4px; }

  .divider {
    position: absolute;
    left: 22px; right: 22px; top: 188px;
    border-top: 1px solid var(--rule);
  }

  .contacts { position: absolute; left: 24px; top: 216px; list-style: none; }
  .contacts li {
    display: flex; align-items: center; gap: 12px;
    font-size: 12px; color: var(--ink); height: 17px;
  }
  .contacts svg { width: 11px; height: 11px; fill: var(--orange); flex: none; }

  .band { position: absolute; bottom: 0; }
  .band--red { left: 0; width: 260px; height: 18px; background: var(--red); }
  .band--orange {
    right: 0; width: 252px; height: 34px;
    background: var(--orange-band);
    clip-path: polygon(14px 0, 100% 0, 100% 100%, 0 100%);
  }
  .web {
    position: absolute; right: 22px; bottom: 10px;
    font-size: 12px; color: #fff;
  }
</style>
</head>
<body>
  <section class="card card--front">
    <div class="brand">
      <span class="brand__dot"></span>
      <span class="brand__name">Steered by Tallies</span>
    </div>
  </section>

  <section class="card card--back">
    <div class="brand">
      <span class="brand__dot"></span>
      <span class="brand__name">Steered by Tallies</span>
    </div>

    <div class="holder">
      <p class="holder__name">Mara T. Ellison</p>
      <p class="holder__title">Managing Director</p>
    </div>

    <div class="divider"></div>

    <ul class="contacts">
      <li>
        <svg viewBox="0 0 12 12" aria-hidden="true"><path d="M1 3.5C1 2 3 1 6 1s5 1 5 2.5V5H8.5V3.8H3.5V5H1z M2.5 6h7l1 5h-9z"/></svg>
        1300 481 481
      </li>
      <li>
        <svg viewBox="0 0 12 12" aria-hidden="true"><path d="M6 0.5a5.5 5.5 0 1 0 0 11a5.5 5.5 0 1 0 0-11zm-0.6 1.3v3.6H2A4.2 4.2 0 0 1 5.4 1.8zm1.2 0A4.2 4.2 0 0 1 10 5.4H6.6zM2 6.6h3.4v3.6A4.2 4.2 0 0 1 2 6.6zm4.6 0H10a4.2 4.2 0 0 1-3.4 3.6z"/></svg>
        mara.ellison@tallyfield.com
      </li>
    </ul>

    <div class="band band--red"></div>
    <div class="band band--orange"></div>
    <span class="web">www.tallyfield.com</span>
  </section>
</body>
</html>
```